Business Card Design Project

Business Card design based on logo.
Updates

I need business card, letterhead, envelope, and if possible, Powerpoint slide template.

On front of business card: Just logo- and  my name and title:  Harriet Lindqvist, Principal

On reverse-logo and the rest of the contact info:

4871 Quarry Lane
Davis, CA 95618
650-318-2764
hl@brackenstudyworks.example

On letterhead-Just logo at top, at bottom  the rest-very small along the bottom

On PPT slide-just the logo.

I also want to try a few other colors-I like lime/dark grey (not black) but would like to try Sienna, maybe also indigo or bright blue-green.

I forgot to add-

On the business card-switch to vertical on reverse side and put:

Reverse side-switch to vertical and list:

Harriet Lindqvist
Principal
Bracken Study Works, LLC

650-318-2764

4871 Quarry Lane
Davis, CA 95618

Harriet Lindqvist
Principal

650-318-2764

4871 Quarry Lane
Davis, CA 95618

I have another project at the same time-for Stationery. Feel free to submit to that one also.

That one includes letterhead, envelope, PPT slide, folder cover sheet-HL

Industry/Entity Type

Business

Requirements
Must have
• Must use logo-preferably lime green version-with gray, not black or just 2-tone -logo on colored background.

```html
<!DOCTYPE html>
<html lang="en">
<head>
<meta charset="utf-8">
<title>Bracken Study Works – Business Cards</title>
<link href="https://fonts.googleapis.com/css2?family=Libre+Baskerville:wght@400;700&family=Cormorant+Garamond:wght@500&family=Jost:wght@400&display=swap" rel="stylesheet">
<style>
  :root {
    --backdrop: #6e3d2b;
    --card: #ffffff;
    --lime: #97b93f;
    --slate: #4a4a4c;
    --ink: #2e2e2e;
    --rule: #9a9a9a;
  }
  * { box-sizing: border-box; margin: 0; padding: 0; }
  html, body { width: 1200px; height: 704px; overflow: hidden; }
  body { background: var(--backdrop); position: relative; }

  .card {
    position: absolute;
    width: 502px; height: 287px;
    border-radius: 18px;
    background: var(--card);
    overflow: hidden;
  }
  .card--front   { left: 84px;  top: 43px; }
  .card--colour  { left: 622px; top: 55px; background: var(--lime); }
  .card--wordmark{ left: 89px;  top: 369px; }
  .card--logo    { left: 622px; top: 373px; }

  .brand-mark {
    position: absolute; left: 50%; transform: translateX(-50%);
    background: var(--lime);
  }
  .brand-name {
    position: absolute; left: 0; right: 0; text-align: center;
    font-family: "Cormorant Garamond", serif; font-weight: 500;
    color: var(--slate); text-transform: uppercase; line-height: 1.05;
  }

  /* Front card */
  .card--front .brand-mark { top: 26px; width: 26px; height: 26px; }
  .card--front .brand-name { top: 70px; font-size: 34px; letter-spacing: 6px; }
  .holder {
    position: absolute; right: 296px; top: 186px; text-align: right;
    font-family: "Libre Baskerville", serif;
  }
  .holder__name { font-size: 18px; font-weight: 700; color: var(--lime); }
  .holder__title { font-size: 13px; color: var(--ink); margin-top: 4px; }
  .divider {
    position: absolute; left: 220px; top: 175px; width: 1px; height: 68px;
    background: var(--rule);
  }
  .contact {
    position: absolute; left: 234px; top: 171px; list-style: none;
    font-family: "Libre Baskerville", serif; font-size: 13px; color: var(--ink);
  }
  .contact li { display: flex; align-items: center; height: 18px; }
  .contact svg { width: 10px; height: 10px; margin-right: 6px; fill: var(--ink); }
  .address {
    position: absolute; left: 0; right: 0; top: 262px; text-align: center;
    font-family: "Libre Baskerville", serif; font-size: 13px; letter-spacing: 0.6px; color: var(--ink);
  }

  .web {
    position: absolute; left: 0; right: 0; top: 248px; text-align: center;
    font-family: "Jost", sans-serif; font-size: 19px; letter-spacing: 3px; color: var(--ink);
  }

  /* Colour card */
  .card--colour .brand-mark { top: 62px; width: 34px; height: 34px; background: var(--card); }
  .card--colour .brand-name { top: 116px; font-size: 40px; letter-spacing: 7px; color: var(--card); }
  .card--colour .web { color: var(--card); }

  /* Wordmark card */
  .card--wordmark .brand-name { top: 78px; font-size: 58px; letter-spacing: 9px; }

  /* Logo card */
  .card--logo .brand-mark { top: 46px; width: 30px; height: 30px; }
  .card--logo .brand-name { top: 104px; font-size: 38px; letter-spacing: 7px; }
</style>
</head>
<body>

<section class="card card--front" aria-label="Business card front">
  <span class="brand-mark"></span>
  <p class="brand-name">Bracken<br>Study Works</p>
  <div class="holder">
    <p class="holder__name">Your Name</p>
    <p class="holder__title">Title</p>
  </div>
  <span class="divider"></span>
  <ul class="contact">
    <li><svg viewBox="0 0 10 10"><path d="M2 0.5 L3.8 2.6 L2.9 3.7 C3.6 5 5 6.4 6.3 7.1 L7.4 6.2 L9.5 8 L8.2 9.5 C4.5 9 1 5.5 0.5 1.8 Z"/></svg>0987 650112</li>
    <li><svg viewBox="0 0 10 10"><rect x="2.5" y="0.5" width="5" height="9" rx="1"/></svg>0987 650112</li>
    <li><svg viewBox="0 0 10 10"><path d="M0.5 2 H9.5 V8.5 H0.5 Z M0.5 2 L5 5.5 L9.5 2" fill="none" stroke="#2e2e2e" stroke-width="1"/></svg>info@brackenstudyworks.example</li>
    <li><svg viewBox="0 0 10 10"><circle cx="5" cy="5" r="4.3" fill="none" stroke="#2e2e2e" stroke-width="1"/><path d="M0.7 5 H9.3 M5 0.7 V9.3" stroke="#2e2e2e" stroke-width="0.8"/></svg>www.brackenstudyworks.example</li>
  </ul>
  <p class="address">00, Complex name, City, State 0042</p>
</section>

<section class="card card--colour" aria-label="Business card back, colour">
  <span class="brand-mark"></span>
  <p class="brand-name">Bracken<br>Study Works</p>
  <p class="web">www.brackenstudyworks.example</p>
</section>

<section class="card card--wordmark" aria-label="Business card back, wordmark">
  <p class="brand-name">Bracken<br>Study Works</p>
  <p class="web">www.brackenstudyworks.example</p>
</section>

<section class="card card--logo" aria-label="Business card back, logo">
  <span class="brand-mark"></span>
  <p class="brand-name">Bracken<br>Study Works</p>
  <p class="web">www.brackenstudyworks.example</p>
</section>

</body>
</html>
```